Re-style home page - eye-catching and unique design for social commerce website

We need a new concept design for BrinoKet's home page.
We don't want to make huge changes but creating a more professional and eye-catching style.

We need to look very serious like a professional services company and in the same time to look like a social network for e-commerce.

Our logo is very captive and you can use to creating something of harmonious.

This is a re-style and I'm excepted to see unique and fresh design like Glimmora.

Target Market(s)

e-commerce and social

Industry/Entity Type

Social

Number of Pages Required

1 page

Font styles to use
Serif
Sans Serif

Requirements
Must have
• An eye-catching result.
• Search bar with logo and Login How it works and business
• The slogan with login and signup.
• Footer links.
Nice to have
• I would like to open the home page and see only two clear ways:
• -Consumer
• --Search
• --The slogan
• --Login and Signup
• --How it works
• -Business
• --Go to Business area
• Background: City, Shopping.
Should not have
• Scrollbar style!

```html
<!DOCTYPE html>
<html lang="en">
<head>
<meta charset="utf-8">
<title>BrinoKet – Shop directly from your profile</title>
<link rel="stylesheet" href="https://fonts.googleapis.com/css2?family=Montserrat:wght@400;500;600;700&family=Open+Sans:wght@300;400&display=swap">
<style>
  :root {
    --night: #1f1d45;
    --night-deep: #16143a;
    --dusk: #3a3766;
    --bar: rgba(22, 22, 52, 0.72);
    --white: #ffffff;
    --field: #ffffff;
    --field-text: #444444;
    --muted: #9a9a9a;
    --red: #d42f2f;
    --green: #7ab531;
    --panel-a: #8fb0b0;
    --panel-b: #6f9494;
    --panel-c: #a7bcbb;
    --avatar-a: #d9b59a;
    --avatar-b: #b98e74;
    --dots: rgba(255, 255, 255, 0.75);
  }
  * { box-sizing: border-box; margin: 0; padding: 0; }
  html, body { width: 1200px; height: 675px; overflow: hidden; }
  body {
    font-family: "Montserrat", Arial, sans-serif;
    color: var(--white);
    background: var(--night-deep);
  }
  .page {
    position: relative;
    width: 1200px;
    height: 675px;
    overflow: hidden;
  }
  .city-backdrop {
    position: absolute;
    inset: 0;
    background:
      radial-gradient(ellipse 60% 45% at 50% 38%, rgba(120, 110, 160, 0.55), transparent 70%),
      radial-gradient(ellipse 40% 50% at 12% 40%, rgba(150, 120, 110, 0.35), transparent 70%),
      radial-gradient(ellipse 35% 45% at 90% 30%, rgba(130, 110, 150, 0.35), transparent 70%),
      linear-gradient(180deg, var(--dusk) 0%, #2c2a5a 45%, var(--night) 75%, var(--night-deep) 100%);
  }

  /* Header */
  .site-header {
    position: absolute;
    top: 0; left: 0;
    width: 1200px;
    height: 58px;
    background: var(--bar);
    display: flex;
    align-items: center;
  }
  .brand {
    position: absolute;
    left: 26px;
    top: 11px;
    font-family: "Montserrat", Arial, sans-serif;
    font-weight: 600;
    font-size: 29px;
    letter-spacing: -0.5px;
    color: var(--white);
    line-height: 36px;
  }
  .feed-label {
    position: absolute;
    left: 295px;
    top: 22px;
    font-size: 11px;
    font-weight: 700;
  }
  .select {
    position: absolute;
    top: 12px;
    height: 34px;
    width: 176px;
    background: var(--field);
    border-radius: 2px;
    color: var(--field-text);
    font-family: "Open Sans", Arial, sans-serif;
    font-size: 12.5px;
    line-height: 34px;
    padding-left: 12px;
  }
  .select-interest { left: 399px; }
  .select-city { left: 584px; padding-left: 28px; }
  .select .chevron { position: absolute; right: 10px; top: 13px; }
  .select .pin { position: absolute; left: 11px; top: 10px; }
  .btn-signup {
    position: absolute;
    left: 773px;
    top: 12px;
    width: 84px;
    height: 34px;
    background: var(--red);
    border-radius: 2px;
    font-size: 13px;
    font-weight: 500;
    text-align: center;
    line-height: 36px;
  }
  .link-login {
    position: absolute;
    left: 871px;
    top: 20px;
    font-size: 13px;
    font-weight: 500;
  }

  /* Connection layer */
  .network {
    position: absolute;
    inset: 0;
  }
  .avatar {
    position: absolute;
    width: 30px;
    height: 30px;
    margin: -15px 0 0 -15px;
    border-radius: 50%;
    border: 2px solid var(--white);
    background: linear-gradient(160deg, var(--avatar-a), var(--avatar-b));
    box-shadow: 0 1px 3px rgba(0,0,0,0.35);
  }

  /* Hero */
  .hero-panel {
    position: absolute;
    left: 350px;
    top: 220px;
    width: 500px;
    height: 152px;
    border-radius: 2px;
    overflow: hidden;
  }
  .hero-photo {
    position: absolute;
    inset: 0;
    background:
      radial-gradient(ellipse 30% 60% at 62% 30%, rgba(60, 70, 75, 0.35), transparent 70%),
      radial-gradient(ellipse 25% 45% at 20% 85%, rgba(200, 215, 210, 0.35), transparent 70%),
      linear-gradient(120deg, var(--panel-c) 0%, var(--panel-a) 45%, var(--panel-b) 100%);
  }
  .hero-title {
    position: absolute;
    top: 20px;
    width: 100%;
    text-align: center;
    font-family: "Open Sans", Arial, sans-serif;
    font-weight: 300;
    font-size: 32px;
    letter-spacing: 0.2px;
  }
  .search-field {
    position: absolute;
    left: 87px;
    top: 78px;
    width: 325px;
    height: 40px;
    background: rgba(255, 255, 255, 0.82);
    border-radius: 2px;
    font-family: "Open Sans", Arial, sans-serif;
    font-size: 13px;
    color: #8a8a8a;
    line-height: 40px;
    padding-left: 17px;
  }
  .search-icon { position: absolute; left: 428px; top: 91px; }

  .btn-business {
    position: absolute;
    left: 511px;
    top: 396px;
    width: 179px;
    height: 34px;
    background: var(--green);
    border-radius: 2px;
    font-size: 12.5px;
    font-weight: 500;
    line-height: 34px;
    text-align: center;
  }
  .btn-business svg { vertical-align: middle; margin-left: 5px; }
  .link-how {
    position: absolute;
    left: 0;
    width: 1200px;
    top: 442px;
    text-align: center;
    font-size: 11.5px;
    font-weight: 500;
  }

  /* Footer */
  .site-footer {
    position: absolute;
    left: 0;
    top: 574px;
    width: 1200px;
    text-align: center;
  }
  .footer-links {
    display: flex;
    justify-content: center;
    gap: 26px;
    list-style: none;
    font-size: 10.5px;
    font-weight: 500;
  }
  .copyright {
    margin-top: 14px;
    font-size: 9.5px;
    font-weight: 500;
  }
</style>
</head>
<body>
<div class="page">
  <div class="city-backdrop" role="img" aria-label="Blurred evening city shopping street with crowds of people"></div>

  <header class="site-header">
    <div class="brand">BrinoKet</div>
    <span class="feed-label">Setup your feed</span>
    <div class="select select-interest">Active life
      <svg class="chevron" width="12" height="8" viewBox="0 0 12 8"><path d="M1 1l5 5 5-5" fill="none" stroke="#b5b5b5" stroke-width="1.4"/></svg>
    </div>
    <div class="select select-city">
      <svg class="pin" width="10" height="14" viewBox="0 0 10 14"><path d="M5 0a5 5 0 0 0-5 5c0 3.8 5 9 5 9s5-5.2 5-9a5 5 0 0 0-5-5zm0 7a2 2 0 1 1 0-4 2 2 0 0 1 0 4z" fill="#b5b5b5"/></svg>
      London
      <svg class="chevron" width="12" height="8" viewBox="0 0 12 8"><path d="M1 1l5 5 5-5" fill="none" stroke="#b5b5b5" stroke-width="1.4"/></svg>
    </div>
    <div class="btn-signup">Sign Up</div>
    <span class="link-login">Login</span>
  </header>

  <svg class="network" width="1200" height="675" viewBox="0 0 1200 675" aria-hidden="true">
    <g fill="none" stroke="var(--dots)" stroke-width="1.4" stroke-dasharray="1.5 3" stroke-linecap="round">
      <path d="M300 194 Q310 232 350 238"/>
      <path d="M362 167 Q382 195 372 220"/>
      <path d="M415 188 Q412 206 405 220"/>
      <path d="M474 184 Q470 204 465 220"/>
      <path d="M684 190 Q692 206 695 220"/>
      <path d="M746 163 Q766 190 768 220"/>
      <path d="M799 184 Q790 204 785 220"/>
      <path d="M860 180 Q850 204 840 220"/>
      <path d="M308 315 Q322 342 350 345"/>
      <path d="M887 298 Q872 330 850 335"/>
      <path d="M303 403 Q316 364 350 360"/>
      <path d="M376 436 Q408 412 412 372"/>
      <path d="M914 356 Q882 368 850 366"/>
      <path d="M795 420 Q762 380 735 376"/>
      <path d="M853 401 Q836 388 828 372"/>
    </g>
  </svg>

  <div class="avatar" style="left:300px;top:194px" role="img" aria-label="Member profile photo"></div>
  <div class="avatar" style="left:362px;top:167px" role="img" aria-label="Member profile photo"></div>
  <div class="avatar" style="left:415px;top:188px" role="img" aria-label="Member profile photo"></div>
  <div class="avatar" style="left:474px;top:184px" role="img" aria-label="Member profile photo"></div>
  <div class="avatar" style="left:684px;top:190px" role="img" aria-label="Member profile photo"></div>
  <div class="avatar" style="left:746px;top:163px" role="img" aria-label="Member profile photo"></div>
  <div class="avatar" style="left:799px;top:184px" role="img" aria-label="Member profile photo"></div>
  <div class="avatar" style="left:860px;top:180px" role="img" aria-label="Member profile photo"></div>
  <div class="avatar" style="left:308px;top:315px" role="img" aria-label="Member profile photo"></div>
  <div class="avatar" style="left:887px;top:298px" role="img" aria-label="Member profile photo"></div>
  <div class="avatar" style="left:303px;top:403px" role="img" aria-label="Member profile photo"></div>
  <div class="avatar" style="left:376px;top:436px" role="img" aria-label="Member profile photo"></div>
  <div class="avatar" style="left:914px;top:356px" role="img" aria-label="Member profile photo"></div>
  <div class="avatar" style="left:795px;top:420px" role="img" aria-label="Member profile photo"></div>
  <div class="avatar" style="left:853px;top:401px" role="img" aria-label="Member profile photo"></div>

  <section class="hero-panel">
    <div class="hero-photo" role="img" aria-label="Close-up fashion photo of a woman wearing sunglasses, in muted teal tones"></div>
    <h1 class="hero-title">Shop directly from your profile</h1>
    <div class="search-field">Search keyword</div>
    <svg class="search-icon" width="20" height="20" viewBox="0 0 20 20" aria-label="Search"><circle cx="8" cy="8" r="6" fill="none" stroke="#fff" stroke-width="2.6"/><path d="M12.5 12.5l5.5 5.5" stroke="#fff" stroke-width="3" stroke-linecap="round"/></svg>
  </section>

  <div class="btn-business">Go to Business Area
    <svg width="20" height="8" viewBox="0 0 20 8"><path d="M0 4h18M14 1l4 3-4 3" fill="none" stroke="#fff" stroke-width="1.1"/></svg>
  </div>
  <div class="link-how">How it works</div>

  <footer class="site-footer">
    <ul class="footer-links">
      <li>About Us</li>
      <li>Blog</li>
      <li>Business</li>
      <li>Jobs</li>
      <li>Privacy</li>
      <li>FAQ</li>
      <li>Contacts</li>
    </ul>
    <p class="copyright">© 2015 BrinoKet. All right reserved.</p>
  </footer>
</div>
</body>
</html>
```